Corvane Capital Business Cards

These are professional business cards that are for my family office.
Put fake emails and phone numbers as of now until I finalize those components. This family office controls my families investments, assets, and future. The cards should be professional.
..
.
.
.
I just uploaded another variation of a logo I would like to see as a business card to I am inbeteen which logo to use

Target Market(s)

business

Industry/Entity Type

business

Contact Information for Business Card

Professional, wealth related, finance related.

Requirements
Must have
• Logo

```html
<!DOCTYPE html>
<html lang="en">
<head>
<meta charset="utf-8">
<title>Corvane Capital Business Cards</title>
<link rel="stylesheet" href="https://fonts.googleapis.com/css2?family=Cinzel:wght@500;600&family=Tinos:wght@400;700&display=swap">
<style>
  :root {
    --backdrop: #ececec;
    --card: #ffffff;
    --ink: #1b1d27;
    --black: #000000;
    --grey: #a8a8a8;
  }
  * { margin: 0; padding: 0; box-sizing: border-box; }
  html, body {
    width: 1200px; height: 716px; overflow: hidden;
    background: var(--backdrop);
  }
  .canvas { position: relative; width: 1200px; height: 716px; }
  .card {
    position: absolute; left: 369px; width: 461px; height: 264px;
    background: var(--card); border-radius: 12px; overflow: hidden;
    border: 1px solid #d6d6d6;
  }
  .card--front { top: 94px; }
  .card--back { top: 386px; }

  .brand-name {
    font-family: "Cinzel", serif; font-weight: 600;
    color: var(--ink); white-space: nowrap; letter-spacing: 0.5px;
  }
  .front-mark {
    position: absolute; left: 164px; top: 43px;
    width: 138px; height: 138px;
  }
  .card--front .brand-name {
    position: absolute; left: 0; right: 0; top: 192px;
    text-align: center; font-size: 25px;
  }
  .card--back .brand-name {
    position: absolute; left: 18px; top: 30px; font-size: 19px;
  }

  .person { position: absolute; left: 18px; top: 108px; font-family: "Tinos", serif; color: var(--black); }
  .person__name { font-size: 18px; font-weight: 700; line-height: 22px; }
  .person__role { font-size: 14px; line-height: 18px; }
  .person__rule { width: 16px; height: 4px; background: var(--black); margin-top: 12px; }

  .contact { position: absolute; left: 18px; top: 180px; font-family: "Tinos", serif; font-size: 13.5px; color: var(--black); list-style: none; }
  .contact li { display: flex; align-items: center; gap: 5px; line-height: 19px; }
  .contact svg { width: 13px; height: 11px; }

  .footer-band { position: absolute; left: 0; right: 0; top: 221px; height: 28px; }
  .footer-band__dark { position: absolute; left: 0; width: 345px; height: 100%; background: var(--black); }
  .footer-band__light { position: absolute; left: 388px; right: 0; height: 100%; background: var(--grey); }
  .footer-badge { position: absolute; left: 343px; top: 211px; width: 48px; height: 48px; }
</style>
</head>
<body>
<main class="canvas">
  <section class="card card--front" aria-label="Card front">
    <svg class="front-mark" viewBox="0 0 138 138" aria-hidden="true">
      <circle cx="69" cy="69" r="66" fill="none" stroke="var(--ink)" stroke-width="4"/>
    </svg>
    <p class="brand-name">Corvane Capital</p>
  </section>

  <section class="card card--back" aria-label="Card back">
    <p class="brand-name">Corvane Capital</p>
    <div class="person">
      <p class="person__name">Daniel Hartley</p>
      <p class="person__role">Founder</p>
      <div class="person__rule"></div>
    </div>
    <ul class="contact">
      <li>
        <svg viewBox="0 0 13 11" aria-hidden="true"><path d="M1 4 C1 1 12 1 12 4 L10 4.5 L9 3 L4 3 L3 4.5 Z M3 5 L10 5 L11.5 10 L1.5 10 Z" fill="var(--black)"/></svg>
        <span>555-014-2290</span>
      </li>
      <li>
        <svg viewBox="0 0 13 11" aria-hidden="true"><rect x="0.5" y="1" width="12" height="9" fill="var(--black)"/><path d="M0.5 1.5 L6.5 6 L12.5 1.5" fill="none" stroke="#fff" stroke-width="1"/></svg>
        <span>office@corvanemail.com</span>
      </li>
    </ul>
    <div class="footer-band">
      <div class="footer-band__dark"></div>
      <div class="footer-band__light"></div>
    </div>
    <svg class="footer-badge" viewBox="0 0 48 48" aria-hidden="true">
      <circle cx="24" cy="24" r="22" fill="var(--card)" stroke="var(--black)" stroke-width="1.5"/>
    </svg>
  </section>
</main>
</body>
</html>
```